Start-Up für Training, Coaching & Consulting sucht modernes Webdesign!
Zielgruppe
Wer ist TAVI Training, Coaching & Consulting?
Wir führen Führungskräftetrainings durch, machen Privatkunden für Bewerbungen fit und unterstützen Unternehmen mit Verkaufstrainings. Wir entwickeln Persönlichkeiten im Coaching. Wir beraten Unternehmen und helfen ihnen dabei, ihre Geschäftsabläufe und Prozesse zu optimieren. Dabei steht unsere hohe Qualität im Mittelpunkt - gemeinsam mit unseren kreativen Trainingsmethoden. Unser Background (Diplom-Kaufleute und geprüfte Trainer) bietet dafür die passende Ausgangslage.
Was bedeutet TAVI?
Tavi ist Maori und bdeutet Kreis/Spirale. Er symbolisiert einen wachsenden Silberfarn und steht für persönliche Entwicklung und Entfaltung. Der Tavi ist einerseits unser Namensgeber und unser Logo, andererseits steht der Tavi aber auch für unsere Werte: Denn wir wollen unseren Kunden dabei helfen zu wachsen und sich weiterzuentwickeln - und dies auf eine hochqualitative und seriöse Art und Weise ohne den Eindruck von Esoterik oder Erlebnispädagogik zu vermitteln.
Aufgabenstellung
Modernes Design, das unsere Philosophie widerspiegelt: Wir möchten unseren Kunden auf seriöse und hochqualitative Weise weiterentwickeln. Wir stehen für nachhaltigen Lernerfolg, kreative Trainingsmethoden, Abwechslung, Spaß am Lernen, Qualität, Kompetenz, Fachwissen und Dynamik.
Layout:
1) Header: QMSR geprüfter Trainer, Menüpunkte (siehe Architektur)
2) Banner
3) 3 Teaser (Training, Coaching, Consulting) + Header + 2-3 Zeilen Text (+Icons)
>>> Sichtbarer Bereich auf Homepage: Menü, Banner, Teaser
4) "Warum Sie uns wählen sollten": 5 bullet points ohne weiteren Text
5) "Aus unserem Blog": Frame für 3 Blogartikel + Bild + Datum + Header + 2-3 Zeilen Text
6) Alle drei QMSR Logos
7) Footer: Click Us (quick links), Contact Us (Adresse), Follow Us (Pinnwald, ZOLP, Kontaktor)
8) Copyright + Impressum
>>> Das Design soll klar sein, aber nicht zu kantig. Vielmehr sollen abgerundete Ecken und dynamische Elemente genutzt werden.
Architektur:
3 Ebenen:
1) Homepage
2) TAVI, Training, Coaching, Consulting, für Trainer, Kundenstimmen/Referenzen, Kontakt
3) noch zu bestimmende Produktdetailseiten
Texte werden noch erstellt, Layout kann ggf. mit Platzhaltertext gefüllt werden.
Bildmaterial: Logo und vorhandenes Imagebild werden zur Verfügung gestellt. Bilder können ggf. gekauft werden. Vorschläge erwünscht.
Corporate colors:
grün: #a2c61b + monochromatic colors
http://www.tintoskop.de/a2c61b
grau: #474747 + monochromatic colors
http://www.tintoskop.de/474747

```html
<!DOCTYPE html>
<html lang="de">
<head>
<meta charset="utf-8">
<title>TAVI Training, Coaching &amp; Consulting</title>
<link href="https://fonts.googleapis.com/css2?family=Questrial&family=Open+Sans:wght@400;600&display=swap" rel="stylesheet">
<style>
:root{
  --green:#a2c61b;
  --green-dark:#8aab12;
  --grey:#474747;
  --night:#2c2e33;
  --night-deep:#1f2024;
  --paper:#efefef;
  --text:#6a6a6a;
  --ink:#2a2a2a;
  --blue:#1f6fb8;
}
html,body{margin:0;padding:0;overflow:hidden;background:#fff;}
.page{position:relative;width:750px;height:1200px;overflow:hidden;font-family:"Open Sans",sans-serif;color:var(--text);}
.page *{box-sizing:border-box;}
.display{font-family:"Questrial",sans-serif;}
/* nav */
.topbar{position:absolute;left:0;top:0;width:750px;height:50px;background:var(--night);}
.brand{position:absolute;left:118px;top:8px;color:#fff;}
.brand-name{font-family:"Questrial",sans-serif;font-size:24px;letter-spacing:1px;line-height:24px;display:flex;align-items:center;gap:5px;}
.brand-name .dot{width:10px;height:10px;border-radius:50%;background:var(--green);display:inline-block;}
.brand-tag{font-size:5px;color:#cfcfcf;margin-top:2px;}
.menu{position:absolute;left:340px;top:0;height:50px;display:flex;font-family:"Questrial",sans-serif;font-size:8.5px;color:#fff;}
.menu a{display:flex;align-items:center;padding:0 10px;color:#fff;text-decoration:none;}
.menu a.active{background:var(--night-deep);color:var(--green);border-top:2px solid var(--green);}
.menu .sep{display:flex;align-items:center;color:#bbb;padding:0 6px;}
.caret{color:var(--green);margin-left:4px;}
/* hero */
.hero{position:absolute;left:0;top:50px;width:750px;height:230px;background:radial-gradient(ellipse at 75% 40%,#8fbd3a 0%,#4f7d22 40%,#2d4e18 75%,#6b5a3a 100%);}
.hero-arrow{position:absolute;top:92px;}
.hero-title{position:absolute;left:94px;top:64px;color:#fff;font-size:24px;line-height:29px;margin:0;font-weight:400;}
.hero-title .chev{color:var(--green);margin-right:3px;}
.hero-title .indent{padding-left:13px;}
.hero-lead{position:absolute;left:108px;top:120px;color:#fff;font-size:11px;line-height:16px;margin:0;}
.btn{position:absolute;left:105px;top:164px;width:95px;height:30px;border-radius:12px;background:var(--green);color:#fff;font-size:7.5px;font-weight:600;display:flex;align-items:center;justify-content:center;}
.rule-green{position:absolute;left:0;width:750px;height:2px;background:var(--green);}
/* intro */
.intro{position:absolute;left:0;top:282px;width:750px;height:284px;background:var(--paper);}
.intro h2{position:absolute;left:0;top:28px;width:750px;text-align:center;font-size:16px;color:var(--ink);margin:0;font-weight:400;}
.intro p{position:absolute;left:58px;top:55px;width:634px;text-align:center;font-size:7px;line-height:12px;margin:0;}
.dotted{position:absolute;border-top:1px dotted #c6d98a;}
.teaser{position:absolute;top:122px;width:160px;text-align:center;}
.teaser .photo{width:104px;height:104px;border-radius:50%;margin:0 auto;}
.teaser h3{font-size:10.5px;line-height:12px;color:var(--ink);margin:14px 0 0;font-weight:400;}
/* main */
.about{position:absolute;left:101px;top:600px;width:290px;}
.about h2{font-size:16px;color:var(--ink);margin:0;font-weight:400;}
.about .dotted{position:relative;width:280px;margin:8px 0 12px;}
.about p{font-size:7.2px;line-height:12px;margin:0 0 8px;}
.about .point{font-weight:600;color:var(--ink);margin:0;position:relative;}
.about .point::before{content:"›";color:var(--green);position:absolute;left:-8px;top:-2px;font-size:10px;}
.side{position:absolute;left:464px;top:600px;width:188px;}
.side h4{font-size:10.5px;color:var(--ink);margin:0;font-weight:400;letter-spacing:.5px;}
.post{display:flex;gap:10px;padding:12px 4px 10px;border-bottom:1px dotted #c6d98a;}
.post .thumb{width:34px;height:34px;border-radius:50%;flex:none;margin-top:4px;}
.post p{font-size:6.2px;line-height:12px;margin:0;}
.more{color:var(--green);font-size:6.2px;}
.news-title{margin-top:18px !important;}
.field{margin-top:10px;height:20px;border-radius:10px;background:#e4e4e4;font-size:6.5px;color:#555;padding:5px 10px;}
/* partners */
.footer{position:absolute;left:0;top:1001px;width:750px;height:148px;background:var(--night);}
.partners{position:absolute;left:129px;top:927px;width:493px;height:96px;border-radius:48px;background:var(--green);}
.badge{position:absolute;background:var(--blue);}
.foot-links{position:absolute;left:101px;top:1053px;font-family:"Questrial",sans-serif;font-size:8.5px;line-height:15px;color:#fff;}
.foot-col{position:absolute;top:1054px;font-size:6.3px;line-height:12px;color:#b9bbc0;}
.foot-col .label{color:var(--green);font-size:7.2px;}
.foot-ico{position:absolute;top:1054px;}
.follow{position:absolute;left:570px;top:1054px;font-family:"Questrial",sans-serif;font-size:8.5px;color:#fff;}
.social{display:flex;gap:6px;margin-top:8px;}
.social span{width:22px;height:22px;border-radius:50%;background:var(--green);display:block;}
.copyright{position:absolute;left:0;top:1148px;width:750px;height:52px;background:var(--night-deep);color:#fff;font-size:7.2px;line-height:12px;text-align:center;padding-top:13px;}
</style>
</head>
<body>
<div class="page">
  <header class="topbar">
    <div class="brand">
      <div class="brand-name">TAVI <span class="dot"></span></div>
      <div class="brand-tag">Training • Coaching • Consulting</div>
    </div>
    <nav class="menu">
      <a class="active">HOME</a><span class="sep">|</span>
      <a>ÜBER UNS<span class="caret">⌄</span></a><span class="sep">|</span>
      <a>FÜR TRAINERS<span class="caret">⌄</span></a><span class="sep">|</span>
      <a>REFERENZEN</a><span class="sep">|</span>
      <a>KONTAKT</a>
    </nav>
  </header>

  <section class="hero" role="img" aria-label="Nahaufnahme eines grünen Farnwedels im Wald">
    <svg class="hero-arrow" style="left:16px" width="28" height="44" viewBox="0 0 28 44"><path d="M22 4 L6 22 L22 40" fill="none" stroke="#a2c61b" stroke-width="7" stroke-linecap="round" stroke-linejoin="round"/></svg>
    <svg class="hero-arrow" style="left:700px" width="28" height="44" viewBox="0 0 28 44"><path d="M6 4 L22 22 L6 40" fill="none" stroke="#a2c61b" stroke-width="7" stroke-linecap="round" stroke-linejoin="round"/></svg>
    <h1 class="hero-title display"><span class="chev">›</span>TRAINING, COACHING<br><span class="indent">CONSULTING FÜR TRAINER</span></h1>
    <p class="hero-lead">Lorem ipsum dolor sit amet consectetur adipiscing elit.<br>Aliquam vehicula, mauris non</p>
    <div class="btn">MEHR ERFAHREN</div>
  </section>
  <div class="rule-green" style="top:280px"></div>

  <section class="intro">
    <h2 class="display">LOREM IPSUM DOLOR SIT AMET, CONSECTETUR ADIPISCING ELIT.</h2>
    <p>Lorem ipsum dolor sit amet, consectetur adipiscing elit. Aliquam vehicula, mauris non eleifend vehicula, lorem turpis fringilla nisi, at feugiat dolor sapien sit amet mauris. In quam dolor, fringilla eget lacinia et, dignissim et purus. Maecenas euismod vel elit nec gravida. Pellentesque pretium ornare lobortis. Aliquam at pulvinar mi. Nulla eget bibendum nisl. Integer consectetur quam ac purus pharetra pulvinar. Aenean faucibus tortor ac tortor aliquet tincidunt. Mauris eget maximus urna.</p>
    <div class="dotted" style="left:120px;top:100px;width:510px"></div>
    <div class="teaser" style="left:119px">
      <div class="photo" role="img" aria-label="Gefaltete Hände auf einem spiegelnden Tisch" style="background:linear-gradient(160deg,#7ea7d6,#d9c3ad 60%,#3b2d28)"></div>
      <h3 class="display">LOREM IPSUM DOLOR SIT<br>AMET MAURIS VOT KALEM</h3>
    </div>
    <div class="teaser" style="left:294px">
      <div class="photo" role="img" aria-label="Zwei Geschäftsleute besprechen sich an einem Tablet" style="background:linear-gradient(160deg,#e6e6e6,#9aa0a8 55%,#2e3440)"></div>
      <h3 class="display">CONSECTETUR ADIPISCING<br>ELIT NON VEHICULA</h3>
    </div>
    <div class="teaser" style="left:469px">
      <div class="photo" role="img" aria-label="Hände mit Tablet bei einer Besprechung" style="background:linear-gradient(160deg,#f4f4f4,#c9d2dc 55%,#6b7a8a)"></div>
      <h3 class="display">DOLOR SIT AMET<br>CONSECTETUR LOREM ELIT</h3>
    </div>
  </section>
  <div class="rule-green" style="top:566px"></div>

  <section class="about">
    <h2 class="display">LOREM IPSUM DOLOR</h2>
    <div class="dotted"></div>
    <p>Vestibulum nec mauris facilisis, suscipit est et, sagittis erat. Duis eget ante rutrum, congue sapien non, accumsan ante. Phasellus vehicula gravida semper. Nulla sapien nisl, mollis in feugiat ac, bibendum vel justo. Morbi et tincidunt erat. Quisque in vestibulum enim. Maecenas imperdiet accumsan libero non gravida. Curabitur et tristique diam, nec sagittis nibh. Nullam vehicula sem eget lectus aliquet, at finibus orci sagittis. Duis sagittis lobortis turpis, et fermentum turpis feugiat at. Vivamus mi felis, convallis non ante venenatis, ornare mattis magna. Ut a tincidunt diam.</p>
    <p class="point">Vestibulum nec mauris facilisis,</p>
    <p>suscipit est et, sagittis erat. Duis eget ante rutrum, congue sapien non, accumsan ante. Phasellus vehicula gravida semper. Nulla sapien nisl, mollis in feugiat ac, bibendum vel justo. Morbi et tincidunt erat. Quisque in vestibulum enim. Maecenas imperdiet accumsan libero non gravida.</p>
    <p class="point">Curabitur et tristique diam, nec sagittis nibh.</p>
    <p>Nullam vehicula sem eget lectus aliquet, at finibus orci sagittis. Duis sagittis lobortis turpis, et fermentum turpis feugiat at. Vivamus mi felis, convallis non ante venenatis, ornare mattis magna. Ut a tincidunt diam. Curabitur commodo ex ut est feugiat, eu sodales massa accumsan.</p>
  </section>

  <aside class="side">
    <h4 class="display">BLOG</h4>
    <div class="post">
      <div class="thumb" role="img" aria-label="Geschäftsleute im Gespräch" style="background:linear-gradient(150deg,#dfe3e8,#5d6673)"></div>
      <div><p>Lorem ipsum dolor sit amet, consectetur adipiscing elit. In dapibus accumsan luctus. Aliquam posuere eros sed nibh sagittis,</p><span class="more">more ›</span></div>
    </div>
    <div class="post">
      <div class="thumb" role="img" aria-label="Porträt eines Trainers" style="background:linear-gradient(150deg,#eceae6,#6d6a66)"></div>
      <div><p>Pellentesque habitant morbi tristique senectus et netus et malesuada fames ac turpis egestas.</p><span class="more">more ›</span></div>
    </div>
    <div class="post">
      <div class="thumb" role="img" aria-label="Hände mit Tablet" style="background:linear-gradient(150deg,#f3f3f3,#8c9aa8)"></div>
      <div><p>Mauris sollicitudin felis aliquam ipsum dictum vehicula. Donec feugiat sapien nunc, quis auctor libero finibus in.</p><span class="more">more ›</span></div>
    </div>
    <h4 class="display news-title">NEWSLETTER ABONNIEREN</h4>
    <div class="field">enter your email id here ...</div>
  </aside>

  <footer class="footer"></footer>
  <div class="partners" role="img" aria-label="Mitgliedschaften und Zertifikate des Verbands QMSR">
    <div class="badge" style="left:66px;top:22px;width:36px;height:46px;border-radius:3px"></div>
    <div class="badge" style="left:208px;top:22px;width:36px;height:46px;border-radius:3px"></div>
    <div class="badge" style="left:340px;top:34px;width:100px;height:26px;border-radius:3px"></div>
  </div>

  <nav class="foot-links">HOME<br>ÜBER UNS<br>FÜR TRAINERS<br>REFERENZEN<br>KONTAKT</nav>

  <svg class="foot-ico" style="left:193px" width="13" height="11" viewBox="0 0 13 11"><path d="M6.5 0 L13 5.5 H11 V11 H8 V7.5 H5 V11 H2 V5.5 H0 Z" fill="#a2c61b"/></svg>
  <div class="foot-col" style="left:217px"><span class="label">Address</span><br>Vestibulum nec mauris 62<br>Suscipit est et<br>62134 Townname</div>

  <svg class="foot-ico" style="left:316px" width="11" height="11" viewBox="0 0 11 11"><rect width="11" height="11" rx="2" fill="#a2c61b"/><path d="M3 2.5 C3 6 5 8 8.5 8.5 L8.5 7 L7 6.3 L6.3 7 C5 6.3 4.5 5.8 4 4.6 L4.7 4 L4 2.5 Z" fill="#2c2e33"/></svg>
  <div class="foot-col" style="left:341px"><span class="label">Phone</span><br>(000) 123 7658 903<br>(000) 123 7658 903<br>(000) 123 7658 903</div>

  <svg class="foot-ico" style="left:429px" width="12" height="9" viewBox="0 0 12 9"><rect width="12" height="9" rx="1" fill="#a2c61b"/><path d="M0.5 0.8 L6 5 L11.5 0.8" fill="none" stroke="#2c2e33" stroke-width="1"/></svg>
  <div class="foot-col" style="left:454px"><span class="label">Email</span><br>info@tavi-coaching.de<br>adresse@tavi-coaching.de<br>post@tavi-coaching.de</div>

  <div class="follow">BITTE FOLGEN
    <div class="social"><span aria-label="Pinnwald"></span><span aria-label="ZOLP"></span><span aria-label="Kontaktor"></span></div>
  </div>

  <div class="copyright">Aliquam at pulvinar mi. Nulla eget bibendum nisl. Integer consectetur quam ac purus pharetra pulvinar.<br>Aenean faucibus tortor ac tortor aliquet tincidunt. Mauris eget maximus urna.</div>
</div>
</body>
</html>
```